Professional Single Page Website Design for Tollbrook Advisory

Tollbrook Advisory is a new business consultancy specializing in providing expert services to small businesses, primarily in the brick-and-mortar retail and food service sectors. We offer a range of services including franchise development and launch, due diligence, and construction management.

Currently, we have a basic website set up at www.tollbrookadvisory.example, but we need a professional touch to enhance its design and functionality.

Project Requirements:
- Single Page Design: For now, we need a single page design that effectively showcases who we are, our services, and contact information.
- Future Expansion: The design should be flexible and scalable for future expansion to include additional pages like specific service offerings, about us, and a dedicated contact page.
- Design Aesthetic: We are looking for a modern yet professional design that aligns with our brand identity.
- Logo: We have a logo that we like, which was also sourced from Pixel Bazaar. The logo files are attached to this project brief.

Key Sections to Include:
- Hero Section: An engaging introduction to Tollbrook Advisory with a strong visual impact.
- About Us: A brief overview of who we are and our mission.
- Team: Section for the profiles of the two principals.
- Services: A clear and concise presentation of our services, including franchise development, due diligence, and construction management.
- Contact Information: Easy-to-find contact details, including a form for inquiries.
- Call to Action: Encouraging visitors to get in touch with us for consultations or further information.

Design Considerations:
- Ensure the design is responsive and mobile-friendly.
- Include high-quality images and icons that complement our services and industry.
- We do not need development services, this is only a design project.

```html
<!DOCTYPE html>
<html lang="en">
<head>
<meta charset="utf-8">
<title>Tollbrook Advisory</title>
<link href="https://fonts.googleapis.com/css2?family=Poppins:wght@400;500;600;700&display=swap" rel="stylesheet">
<style>
:root{
  --green:#8fc7ae;
  --green-soft:#e9f3ee;
  --ink:#29333d;
  --text:#6f7479;
  --white:#ffffff;
  --line:#d9dcdf;
}
*{box-sizing:border-box;margin:0;padding:0}
html,body{width:1200px;height:2990px;overflow:hidden;background:var(--white)}
body{position:relative;font-family:'Poppins',sans-serif;color:var(--ink)}
.abs{position:absolute}
.topline{left:0;top:0;width:1200px;height:4px;background:var(--green)}
.brand{left:145px;top:26px;display:flex;align-items:center;gap:12px}
.brand-dot{width:46px;height:46px;border-radius:50%;background:var(--green)}
.brand-name{font-size:25px;font-weight:600;color:var(--ink);line-height:1}
.nav{right:145px;top:32px;display:flex;align-items:center;gap:34px;font-size:13px;font-weight:600}
.nav a{color:var(--ink);text-decoration:none}
.login{background:var(--green);color:var(--white)!important;border-radius:20px;padding:11px 29px}
.hero-img{left:0;top:102px;width:1200px;height:623px}
.hero-dots{left:1127px;top:258px;display:flex;flex-direction:column;gap:12px}
.hero-dots span{width:8px;height:8px;background:var(--white);transform:rotate(45deg)}
.hero-dots span.on{background:var(--green)}
.hero-text{left:400px;top:368px;width:400px;text-align:center}
.hero-text .w{font-size:32px;font-weight:700;line-height:1.1}
.hero-text .n1{font-size:54px;font-weight:700;line-height:1}
.hero-text .n2{font-size:54px;font-weight:700;line-height:1.05;color:var(--green)}
.btn{display:inline-block;background:var(--ink);color:var(--white);font-weight:600;font-size:15px;border-radius:28px;text-align:center}
.hero-btn{left:527px;top:532px;width:147px;height:52px;line-height:52px}
.about-art{left:100px;top:640px;width:330px;height:470px;background:linear-gradient(#f2f6f5,#f6f8f8)}
.about-title{left:145px;top:787px;font-size:50px;font-weight:700}
.about-title span{color:var(--green)}
.tabs{left:145px;top:866px;display:flex;gap:40px;font-size:16px;font-weight:600;color:#777}
.tabs .act{color:var(--green);border-bottom:3px solid var(--green);padding-bottom:6px}
.about-copy{left:512px;top:791px;width:544px;font-size:15.5px;line-height:24px;color:var(--text);text-align:justify}
.about-btn{left:512px;top:1060px;width:148px;height:52px;line-height:52px}
.team-title{left:0;top:1290px;width:1200px;text-align:center;font-size:50px;font-weight:700}
.team-title span,.svc-title span{color:var(--green)}
.card{width:350px;height:212px;border:2px solid #e6e8ea;background:var(--white)}
.card-body{position:absolute;left:110px;top:22px;width:220px}
.card h3{font-size:18px;font-weight:700;text-transform:uppercase}
.card .role{color:var(--green);font-size:16px;margin:4px 0 14px}
.card p{font-size:12.5px;line-height:20px;color:var(--text)}
.card .more{display:inline-block;margin-top:10px;font-size:13px;font-weight:700;text-decoration:underline;color:var(--ink)}
.photo{width:130px;height:130px;transform:rotate(45deg)}
.dark{left:0;top:1690px;width:1200px;height:800px;background:var(--ink)}
.svc-title{left:0;top:1765px;width:1200px;text-align:center;font-size:50px;font-weight:700;color:var(--white)}
.svc{width:294px;height:300px;border:1px solid #8a9299;padding:7px}
.svc-in{width:100%;height:100%;border:2px solid var(--white);text-align:center;color:var(--white);padding:22px 20px 0}
.svc-in svg.ic{height:66px;display:block;margin:0 auto 22px}
.svc-in h4{font-size:15px;font-weight:700;margin-bottom:12px}
.svc-in p{font-size:12px;line-height:20px}
.svc-in .down{display:block;margin:14px auto 0}
.foot-name{left:0;top:2470px;width:1200px;text-align:center;font-size:33px;font-weight:500;color:var(--ink)}
.foot-mark{left:518px;top:2298px;width:164px;height:164px;border-radius:50%;background:var(--green)}
.h-sm{font-size:24px;font-weight:500}
.ci{display:flex;align-items:center;gap:16px;font-size:13.5px;color:#444;line-height:22px}
.ci .c{width:46px;height:46px;border-radius:50%;border:1px solid #ddd;display:flex;align-items:center;justify-content:center;flex:none}
.ci .c.fill{background:var(--ink);border-color:var(--ink)}
.socials{left:163px;top:2844px;display:flex;gap:8px}
.socials span{width:33px;height:33px;border-radius:50%;border:2px solid var(--ink)}
.vline{left:516px;top:2582px;width:1px;height:320px;background:#e5e7e8}
.field{border:1px solid #c9cccf;font-size:13.5px;color:#555;padding:14px 23px;background:var(--white)}
.copy{left:163px;top:2954px;font-size:13px;color:#444}
</style>
</head>
<body>
<div class="abs topline"></div>
<header>
  <div class="abs brand"><span class="brand-dot"></span><span class="brand-name">Tollbrook Advisory</span></div>
  <nav class="abs nav">
    <a href="#">HOME</a><a href="#">ABOUT US</a><a href="#">TEAM</a><a href="#">SERVICES</a><a href="#">CONTACT</a><a href="#" class="login">LOGIN</a>
  </nav>
</header>

<section class="hero">
  <svg class="abs hero-img" viewBox="0 102 1200 623" width="1200" height="623" role="img" aria-label="City skyline at sunset over a lake and hillside homes">
    <defs>
      <linearGradient id="sky" x1="0" y1="0" x2="0" y2="1">
        <stop offset="0" stop-color="#b6b3b4"/>
        <stop offset=".45" stop-color="#c9a68e"/>
        <stop offset=".75" stop-color="#7d6a55"/>
        <stop offset="1" stop-color="#55584c"/>
      </linearGradient>
    </defs>
    <polygon points="0,102 1200,102 1200,495 600,725 0,495" fill="url(#sky)"/>
    <polygon points="600,240 830,470 600,700 370,470" fill="var(--green)"/>
    <polygon points="600,272 798,470 600,668 402,470" fill="var(--white)"/>
  </svg>
  <div class="abs hero-dots"><span></span><span class="on"></span><span></span></div>
  <div class="abs hero-text">
    <div class="w">Welcome to</div>
    <div class="n1">Tollbrook</div>
    <div class="n2">Advisory</div>
  </div>
  <a class="abs btn hero-btn">GET STARTED</a>
</section>

<section class="about">
  <div class="abs about-art" role="img" aria-label="Faint illustration of office towers"></div>
  <h2 class="abs about-title">About <span>Us</span></h2>
  <div class="abs tabs"><span class="act">WHO WE ARE</span><span>MISSION</span></div>
  <p class="abs about-copy">Welcome to Tollbrook Advisory, your trusted partner in navigating the complexities of the real estate and small business markets. Founded by industry veterans Dario Velasco and Evan Hollis, we specialize in providing comprehensive services tailored to the unique needs of our clients. Whether you're a franchisee, a new restaurant owner, or a commercial real estate investor, our expertise in due diligence, construction management, and investment property evaluation ensures you make informed, strategic decisions.At Tollbrook Advisory, we are committed to your success. Our approach combines meticulous analysis, strategic insights, and personalized service to help you achieve your business goals.</p>
  <a class="abs btn about-btn">READ MORE</a>
</section>

<section class="team">
  <svg class="abs" style="left:0;top:1160px" width="1200" height="250" viewBox="0 1160 1200 250">
    <polyline points="0,1405 607,1168 1200,1405" fill="none" stroke="var(--green)" stroke-width="4"/>
  </svg>
  <h2 class="abs team-title">Our <span>Team</span></h2>

  <div class="abs card" style="left:235px;top:1391px">
    <div class="card-body">
      <h3>Evan Hollis</h3>
      <div class="role">Principal</div>
      <p>Evan Hollis is a seasoned real estate expert with extensive experience in project and construction</p>
      <a class="more">READ MORE</a>
    </div>
  </div>
  <div class="abs photo" role="img" aria-label="Portrait of Evan Hollis" style="left:172px;top:1432px;background:linear-gradient(135deg,#6b5640,#9a7a5c)"></div>

  <div class="abs card" style="left:708px;top:1391px">
    <div class="card-body">
      <h3>Dario Velasco</h3>
      <div class="role">Principal</div>
      <p>Dario Velasco brings almost 20 years of rich experience as a real estate investor and a pivotal role</p>
      <a class="more">READ MORE</a>
    </div>
  </div>
  <div class="abs photo" role="img" aria-label="Portrait of Dario Velasco" style="left:645px;top:1432px;background:linear-gradient(135deg,#7fa7c9,#e6e8ee)"></div>
</section>

<section class="services">
  <div class="abs dark"></div>
  <h2 class="abs svc-title">Our <span>Services</span></h2>
  <svg class="abs" style="left:62px;top:1983px" width="36" height="66"><polyline points="34,2 2,33 34,64" fill="none" stroke="#9aa1a7" stroke-width="2"/></svg>
  <svg class="abs" style="left:1102px;top:1983px" width="36" height="66"><polyline points="2,2 34,33 2,64" fill="none" stroke="#9aa1a7" stroke-width="2"/></svg>

  <div class="abs svc" style="left:141px;top:1866px"><div class="svc-in">
    <svg class="ic" viewBox="0 0 84 50" width="84"><rect x="0" y="16" width="8" height="26" fill="#fff"/><rect x="76" y="16" width="8" height="26" fill="#fff"/><path d="M12 18 L30 8 L46 14 L56 8 L72 18 L72 38 L58 46 L30 46 L12 36Z" fill="#fff"/><path d="M30 20 L44 32 L56 26" fill="none" stroke="var(--ink)" stroke-width="4"/></svg>
    <h4>FRANCHISE DEVELOPMENT</h4>
    <p>At Tollbrook Advisory, our Franchise Development &amp; Launch service is designed to transform your successful business into a thriving franchise.</p>
    <svg class="down" width="30" height="30"><circle cx="15" cy="15" r="13" fill="none" stroke="var(--green)" stroke-width="1.5"/><path d="M15 8v14M9 16l6 6 6-6" fill="none" stroke="var(--green)" stroke-width="1.5"/></svg>
  </div></div>

  <div class="abs svc" style="left:453px;top:1866px"><div class="svc-in">
    <svg class="ic" viewBox="0 0 84 66" width="84"><circle cx="28" cy="36" r="20" fill="#fff" stroke="#fff" stroke-width="8" stroke-dasharray="6 5"/><circle cx="28" cy="36" r="8" fill="var(--ink)"/><circle cx="66" cy="14" r="10" fill="#fff"/><circle cx="66" cy="14" r="4" fill="var(--ink)"/><circle cx="66" cy="52" r="10" fill="#fff"/><circle cx="66" cy="52" r="4" fill="var(--ink)"/></svg>
    <h4>DUE DILIGENCE</h4>
    <p>Tollbrook Advisory offers comprehensive evaluations tailored to your business needs. We meticulously assess franchise opportunities.</p>
    <svg class="down" width="30" height="30"><circle cx="15" cy="15" r="13" fill="none" stroke="var(--green)" stroke-width="1.5"/><path d="M15 8v14M9 16l6 6 6-6" fill="none" stroke="var(--green)" stroke-width="1.5"/></svg>
  </div></div>

  <div class="abs svc" style="left:765px;top:1866px"><div class="svc-in">
    <svg class="ic" viewBox="0 0 56 66" width="56"><rect x="4" y="0" width="48" height="62" fill="#fff"/><rect x="0" y="60" width="56" height="6" fill="#fff"/><g fill="var(--ink)"><rect x="14" y="8" width="8" height="8"/><rect x="34" y="8" width="8" height="8"/><rect x="14" y="22" width="8" height="8"/><rect x="34" y="22" width="8" height="8"/><rect x="14" y="36" width="8" height="8"/><rect x="34" y="36" width="8" height="8"/><rect x="24" y="50" width="8" height="12"/></g></svg>
    <h4>CONSTRUCTION MANAGEMENT</h4>
    <p>Our Building &amp; Construction Management Services oversee every aspect of your construction and development projects.</p>
    <svg class="down" width="30" height="30"><circle cx="15" cy="15" r="13" fill="none" stroke="var(--green)" stroke-width="1.5"/><path d="M15 8v14M9 16l6 6 6-6" fill="none" stroke="var(--green)" stroke-width="1.5"/></svg>
  </div></div>
</section>

<footer>
  <svg class="abs" style="left:0;top:2240px" width="1200" height="260" viewBox="0 2240 1200 260">
    <polygon points="0,2490 0,2487 607,2250 1200,2487 1200,2500 0,2500" fill="var(--white)"/>
    <polyline points="0,2487 607,2250 1200,2487" fill="none" stroke="var(--green)" stroke-width="5"/>
  </svg>
  <div class="abs foot-mark"></div>
  <div class="abs foot-name">Tollbrook Advisory</div>

  <h3 class="abs h-sm" style="left:163px;top:2572px">Contact Info</h3>
  <div class="abs ci" style="left:163px;top:2625px">
    <span class="c"><svg width="18" height="18" viewBox="0 0 24 24"><path d="M6 2l4 5-2 3c1 3 3 5 6 6l3-2 5 4-3 4C10 21 3 14 2 5z" fill="var(--green)"/></svg></span>
    <span>Phone: +1 555 014 2290</span></div>
  <div class="abs ci" style="left:163px;top:2685px">
    <span class="c fill"><svg width="20" height="16" viewBox="0 0 20 16"><rect width="20" height="16" rx="2" fill="#fff"/><path d="M1 2l9 7 9-7" fill="none" stroke="var(--ink)" stroke-width="2"/></svg></span>
    <span>hello@tollbrookadvisory.example</span></div>
  <div class="abs ci" style="left:163px;top:2745px">
    <span class="c"><svg width="18" height="18"><circle cx="9" cy="9" r="7" fill="none" stroke="var(--green)" stroke-width="1.5"/><path d="M9 5v4l3 2" fill="none" stroke="var(--green)" stroke-width="1.5"/></svg></span>
    <span>214 Meridian Way Suite 300<br>214 Meridian Way, Larkfield, CA 90410</span></div>
  <div class="abs socials" aria-label="Social links"><span></span><span></span><span></span><span></span><span></span></div>

  <div class="abs vline"></div>

  <h3 class="abs h-sm" style="left:610px;top:2572px">Get In Touch</h3>
  <div class="abs field" style="left:610px;top:2636px;width:208px;height:45px">Enter Name</div>
  <div class="abs field" style="left:829px;top:2636px;width:208px;height:45px">Enter Email</div>
  <div class="abs field" style="left:610px;top:2693px;width:208px;height:45px">Phone</div>
  <div class="abs field" style="left:829px;top:2693px;width:208px;height:45px">Address</div>
  <div class="abs field" style="left:610px;top:2750px;width:427px;height:93px">Message</div>
  <a class="abs btn" style="left:610px;top:2855px;width:149px;height:52px;line-height:52px">SUBMIT</a>

  <p class="abs copy">© 2024 Tollbrook Advisory . All rights reserved.Privacy Terms of Use</p>
  <div class="abs" style="left:0;top:2986px;width:1200px;height:4px;background:var(--green)"></div>
</footer>
</body>
</html>
```